Velloway Air Business Card Design

Design new, 2 sides, business cards for a residential and light commercial heating, air conditioning contractor.

Target Market(s)

Homeowners, small businesses

Industry/Entity Type

Business

Contact Information for Business Card

Dominic Westerhall
Phone - 862-415-2736
Email
Address - PO box 518
Brightwater NJ 07912
Website - www.HarborBreezeLLC.example

Requirements
Must have
• logo, company colors, standard size with no die cut, so I can use nova stamp

```html
<!DOCTYPE html>
<html lang="en">
<head>
<meta charset="utf-8">
<title>Velloway Air Business Card</title>
<link href="https://fonts.googleapis.com/css2?family=Open+Sans:wght@400;700&display=swap" rel="stylesheet">
<style>
  :root {
    --page-bg: #ececec;
    --card-white: #fbfbfa;
    --brand-red: #9e2435;
    --brand-orange: #f0a030;
    --brand-cream: #fbf1d9;
    --ink: #3a3a3a;
    --ink-soft: #5a5a5a;
  }
  * { margin: 0; padding: 0; box-sizing: border-box; }
  html, body {
    width: 1200px;
    height: 900px;
    overflow: hidden;
    background: var(--page-bg);
    font-family: "Open Sans", Arial, sans-serif;
  }
  .card-sheet {
    width: 1200px;
    height: 900px;
    display: flex;
    align-items: center;
    justify-content: center;
    gap: 50px;
  }
  .card {
    width: 525px;
    height: 300px;
    position: relative;
    overflow: hidden;
    box-shadow: 0 6px 18px rgba(0,0,0,0.12);
  }
  .card--front { background: var(--card-white); }
  .card--back {
    background: var(--brand-red);
    display: flex;
    align-items: center;
    justify-content: center;
  }

  .contact-block {
    position: absolute;
    left: 34px;
    top: 34px;
    width: 210px;
    color: var(--ink);
  }
  .contact-name {
    color: var(--brand-red);
    font-weight: 700;
    font-size: 17px;
    line-height: 1.2;
  }
  .contact-title {
    font-size: 12px;
    color: var(--ink-soft);
    margin-bottom: 8px;
  }
  .contact-list { list-style: none; }
  .contact-item {
    display: flex;
    align-items: flex-start;
    gap: 7px;
    font-size: 12px;
    line-height: 1.45;
    white-space: nowrap;
  }
  .contact-icon {
    width: 10px;
    height: 10px;
    margin-top: 4px;
    flex: none;
    fill: var(--brand-red);
  }

  .brand-name {
    display: flex;
    align-items: center;
    gap: 10px;
    font-family: "Open Sans", Arial, sans-serif;
    font-weight: 700;
    white-space: nowrap;
    line-height: 1;
  }
  .brand-mark {
    border-radius: 50%;
    background: var(--brand-orange);
    flex: none;
  }
  .card--front .brand-name {
    position: absolute;
    right: 36px;
    top: 168px;
    font-size: 30px;
    color: var(--brand-red);
  }
  .card--front .brand-mark { width: 24px; height: 24px; }
  .card--back .brand-name {
    font-size: 40px;
    color: var(--brand-cream);
  }
  .card--back .brand-mark { width: 32px; height: 32px; }
</style>
</head>
<body>
<main class="card-sheet">

  <section class="card card--front" aria-label="Card front">
    <div class="contact-block">
      <p class="contact-name">Dominic Westerhall</p>
      <p class="contact-title">Managing Director</p>
      <ul class="contact-list">
        <li class="contact-item">
          <svg class="contact-icon" viewBox="0 0 10 10"><path d="M2 0.5h2l1 2.5-1.3 1a5 5 0 0 0 2.3 2.3l1-1.3 2.5 1v2a1 1 0 0 1-1 1A8.5 8.5 0 0 1 1 1.5a1 1 0 0 1 1-1z"/></svg>
          <span>862-415-2736</span>
        </li>
        <li class="contact-item">
          <svg class="contact-icon" viewBox="0 0 10 10"><rect x="2.5" y="0" width="5" height="10" rx="1"/></svg>
          <span>862-415-2736</span>
        </li>
        <li class="contact-item">
          <svg class="contact-icon" viewBox="0 0 10 10"><path d="M0 2h10v6H0z M0 2l5 3.5L10 2" stroke="#fbfbfa" stroke-width="0.8"/></svg>
          <span>info@vellowayairllc.example</span>
        </li>
        <li class="contact-item">
          <svg class="contact-icon" viewBox="0 0 10 10"><circle cx="5" cy="5" r="5"/></svg>
          <span>www.VellowayAirLLC.example</span>
        </li>
        <li class="contact-item">
          <svg class="contact-icon" viewBox="0 0 10 10"><path d="M5 0a3.5 3.5 0 0 1 3.5 3.5C8.5 6 5 10 5 10S1.5 6 1.5 3.5A3.5 3.5 0 0 1 5 0z"/></svg>
          <span>PO box 518,<br>Brightwater NJ 07912</span>
        </li>
      </ul>
    </div>
    <p class="brand-name"><span class="brand-mark"></span>Velloway Air</p>
  </section>

  <section class="card card--back" aria-label="Card back">
    <p class="brand-name"><span class="brand-mark"></span>Velloway Air</p>
  </section>

</main>
</body>
</html>
```